Local Flower Farm Needs Business Card Design

I need business cards designed for a flower farm based in Eudora, Kansas.
Business Info:
We are a local cut flower farm located in Eudora, Kansas, founded by Corinne Haldwick. What started as a passion for agriculture and search for more joy in daily life has blossomed into a small business dedicated to providing the community with beautiful, fresh, and sustainable flowers. We specialize in local, seasonal blooms, ensuring that every petal reflects the care and dedication we pour into our craft. Our mission is to deliver the highest quality flowers directly to our customers through local farmers markets and to florists who share our commitment to sustainability. Join us in celebrating the beauty of nature, one bloom at a time!
Contact Details:
Corinne Haldwick
Owner
Phone 913-555-0147
Facebook: Rosalind Thorpe Gardens
Instagram: @RosalindThorpeGardens
Website: RosalindThorpeGardens.example
Target Market(s)
Wholesale to Florists and Direct to Consumer via Farmers Market
Industry/Entity Type
Florist, Farm
Contact Information for Business Card
Name, Contact Info, Logo
Look and feel
Each slider illustrates characteristics of the customer's brand and the style your logo design should communicate.

```html
<!DOCTYPE html>
<html lang="en">
<head>
<meta charset="utf-8">
<title>Rosalind Thorpe Gardens – Business Card</title>
<link href="https://fonts.googleapis.com/css2?family=Playfair+Display:wght@400;600&family=Lato:wght@400&display=swap" rel="stylesheet">
<style>
  :root {
    --backdrop: #2e2f30;
    --teal-deep: #0c2a2d;
    --teal-mid: #1d4a4e;
    --silver: #c9cdd0;
    --paper: #ffffff;
    --ink: #0f2e31;
    --ink-soft: #3d4f51;
  }
  * { margin: 0; padding: 0; box-sizing: border-box; }
  html, body { width: 1200px; height: 875px; overflow: hidden; }
  body {
    background: var(--backdrop);
    position: relative;
    font-family: "Lato", sans-serif;
  }
  .card {
    position: absolute;
    top: 283px;
    width: 540px;
    height: 309px;
    border-radius: 22px;
    overflow: hidden;
  }
  /* Back side */
  .card--back { left: 40px; background: var(--teal-deep); }
  .seal {
    position: absolute;
    left: 50%; top: 50%;
    width: 200px; height: 200px;
    transform: translate(-50%, -50%);
    border: 1.5px solid var(--silver);
    border-radius: 50%;
    display: flex; align-items: center; justify-content: center;
    text-align: center;
  }
  .seal__name {
    font-family: "Playfair Display", serif;
    font-weight: 400;
    color: var(--silver);
    font-size: 19px;
    letter-spacing: 3px;
    line-height: 1.45;
    text-transform: uppercase;
  }
  /* Front side */
  .card--front { left: 620px; background: var(--paper); }
  .botanical-art {
    position: absolute;
    left: 0; top: 0;
    width: 245px; height: 100%;
    background: linear-gradient(135deg, var(--teal-deep) 0%, var(--teal-mid) 55%, #e8eeee 100%);
    border-radius: 0 40px 0 0;
  }
  .details {
    position: absolute;
    left: 280px; top: 46px;
    color: var(--ink);
  }
  .details__name {
    font-family: "Playfair Display", serif;
    font-weight: 600;
    font-size: 25px;
    letter-spacing: 1.5px;
    line-height: 1.05;
    text-transform: uppercase;
  }
  .details__role {
    font-size: 14px;
    color: var(--ink-soft);
    margin-top: 6px;
  }
  .details__rule {
    width: 30px; height: 2px;
    background: var(--ink);
    margin: 12px 0 18px;
  }
  .contact-list { list-style: none; }
  .contact-list li {
    display: flex; align-items: center;
    font-size: 13px;
    color: var(--ink-soft);
    margin-bottom: 9px;
    white-space: nowrap;
  }
  .contact-list svg { width: 11px; height: 11px; margin-right: 10px; flex: none; }
</style>
</head>
<body>
  <section class="card card--back" aria-label="Business card back">
    <div class="seal">
      <p class="seal__name">Rosalind<br>Thorpe<br>Gardens</p>
    </div>
  </section>

  <section class="card card--front" aria-label="Business card front">
    <div class="botanical-art" role="img" aria-label="Large monogram with line-drawn flowering stems"></div>
    <div class="details">
      <h1 class="details__name">Corinne<br>Haldwick</h1>
      <p class="details__role">Owner</p>
      <div class="details__rule"></div>
      <ul class="contact-list">
        <li>
          <svg viewBox="0 0 12 12" aria-hidden="true"><path d="M2.5 1 L4.5 1 L5.2 3.4 L4 4.3 Q5 6.8 7.7 8 L8.6 6.8 L11 7.5 L11 9.5 Q10.5 11 9 11 Q1 10 1 2.5 Q1 1 2.5 1 Z" fill="var(--ink)"/></svg>
          913-555-0147
        </li>
        <li>
          <svg viewBox="0 0 12 12" aria-hidden="true"><rect x="1" y="1" width="10" height="10" fill="var(--ink)"/></svg>
          Rosalind Thorpe Gardens
        </li>
        <li>
          <svg viewBox="0 0 12 12" aria-hidden="true"><circle cx="6" cy="6" r="5" fill="none" stroke="var(--ink)" stroke-width="1.4"/></svg>
          @RosalindThorpeGardens
        </li>
        <li>
          <svg viewBox="0 0 12 12" aria-hidden="true"><circle cx="6" cy="6" r="5" fill="none" stroke="var(--ink)" stroke-width="1.2"/><ellipse cx="6" cy="6" rx="2.2" ry="5" fill="none" stroke="var(--ink)" stroke-width="1"/><line x1="1" y1="6" x2="11" y2="6" stroke="var(--ink)" stroke-width="1"/></svg>
          RosalindThorpeGardens.example
        </li>
      </ul>
    </div>
  </section>
</body>
</html>
```